IT Company based on Biology Business Needs a Professional Web Design

We need a professional business website design for a new company called 'Plume KEV'. We develop the machine learning solutions especially focused on deep learning algorithms for biology industry. Our initial product is a vision detection on biological images to help doctors diagnose the symptoms. We would like to see designs that use the color green.

Industry/Entity Type

Business

Number of Pages Required

5+ page

```html
<!DOCTYPE html>
<html lang="en">
<head>
<meta charset="utf-8">
<title>Plume KEV</title>
<link href="https://fonts.googleapis.com/css2?family=Open+Sans:ital,wght@0,400;0,600;0,700;1,400&display=swap" rel="stylesheet">
<style>
:root{
  --green:#0f8a5a;
  --green-dark:#0b6f48;
  --green-light:#3fae49;
  --ink:#1f1f1f;
  --muted:#6b6b6b;
  --dark:#1c1e21;
  --footer-bar:#222;
  --white:#fff;
  --soft:#f2f3f4;
}
*{margin:0;padding:0;box-sizing:border-box}
html,body{width:1200px;height:2857px;overflow:hidden}
body{font-family:"Open Sans",Arial,sans-serif;color:var(--ink);background:var(--white);position:relative}
.abs{position:absolute}
.center{text-align:center;left:0;width:1200px}

/* hero */
.hero{top:0;left:0;width:1200px;height:652px;background:radial-gradient(circle at 75% 40%,#c9ced6 0%,#7d8592 35%,#3a3f48 75%,#23262c 100%)}
.brand{top:44px;left:84px;display:flex;align-items:center;gap:10px;color:var(--green-light);font-weight:700;font-size:28px;letter-spacing:-.5px}
.brand-dot{width:16px;height:16px;border-radius:50%;background:var(--green-light)}
.nav{top:60px;left:448px;display:flex;gap:31px;font-size:13px;color:var(--white);text-transform:uppercase}
.nav .active{border-bottom:2px solid var(--white);padding-bottom:6px}
.login{top:48px;left:1037px;width:76px;height:40px;border:1px solid var(--white);border-radius:3px;color:var(--white);font-size:13px;display:flex;align-items:center;justify-content:center}
.hero-title{top:306px;font-size:50px;font-weight:700;color:var(--white)}
.hero-sub{top:372px;font-size:20px;color:#eee;line-height:33px}
.btn-outline{border:1px solid var(--white);color:var(--white);font-size:14px;font-weight:600;display:flex;align-items:center;justify-content:center;text-transform:uppercase}
.hero-btn{top:466px;left:514px;width:172px;height:45px}
.arrow{width:34px;height:34px;border-radius:50%;background:rgba(0,0,0,.55);display:flex;align-items:center;justify-content:center;top:332px}

/* services */
.services{top:652px;left:0;width:1200px;height:416px;background:linear-gradient(135deg,#f6f6f6,#ececec 50%,#f7f7f7)}
.section-title{font-size:27px;font-weight:600;text-transform:uppercase}
.section-title span{color:var(--green)}
.section-sub{font-size:15px;color:var(--muted)}
.service{width:300px;text-align:center;top:795px}
.ring{width:122px;height:122px;border-radius:50%;border:2px solid #555;background:var(--white);margin:0 auto;display:flex;align-items:center;justify-content:center}
.service h3{margin-top:30px;font-size:16px;font-weight:600;text-transform:uppercase}
.service p{margin-top:6px;font-size:12.5px;color:var(--muted);line-height:19px}

/* solutions */
.solutions{top:1068px;left:0;width:1200px;height:547px;background:linear-gradient(135deg,#14985f,#0c7e51)}
.monitor{top:1240px;left:90px;width:388px;height:258px;background:#111;border-radius:10px;padding:14px}
.monitor-screen{width:100%;height:100%;background:#f3f3f3;display:flex;align-items:center;justify-content:center;gap:12px;color:var(--green-light);font-weight:700;font-size:40px}
.stand{top:1498px;left:240px;width:88px;height:50px;background:linear-gradient(#e5e5e5,#bdbdbd)}
.base{top:1546px;left:222px;width:124px;height:10px;background:#cfcfcf;border-radius:5px}
.sol-text{top:1244px;left:517px;width:590px;color:var(--white)}
.sol-text h2{font-size:22px;font-weight:400;margin-bottom:20px}
.sol-text p{font-size:12.5px;line-height:24px;margin-bottom:16px}
.sol-btn{top:1458px;left:516px;width:114px;height:35px;border-radius:2px}

/* testimonial */
.testimonial{top:1615px;left:0;width:1200px;height:335px;background:linear-gradient(90deg,#15181c,#262a2f 60%,#1a1d21)}
.avatar{top:1674px;left:542px;width:116px;height:116px;border-radius:50%;border:4px solid var(--white);background:linear-gradient(#b9a08a,#6d5a4a)}
.quote{top:1790px;left:165px;width:870px;text-align:center;color:var(--white);font-size:13.5px;line-height:23px}
.qmark{font-size:40px;line-height:40px;color:var(--white);font-family:Georgia,serif}
.author{top:1864px;color:#ddd;font-size:13px;font-style:italic;line-height:22px}

/* products */
.products{top:1950px;left:0;width:1200px;height:468px;background:linear-gradient(135deg,#f6f6f6,#ededed 50%,#f6f6f6)}
.card{top:2098px;width:249px;height:262px;background:var(--white);box-shadow:0 1px 4px rgba(0,0,0,.12)}
.card-img{height:160px}
.card h4{font-size:14px;font-weight:600;padding:16px 16px 0}
.card p{font-size:11.5px;color:var(--muted);line-height:20px;padding:8px 16px 0}

/* partners */
.partners{top:2418px;left:0;width:1200px;height:152px;background:var(--white)}
.partner{top:2486px;width:140px;height:34px;border-radius:17px;background:#d6d6d6}

/* footer */
.footer{top:2570px;left:0;width:1200px;height:223px;background:var(--green)}
.fcol{top:2604px;color:var(--white)}
.fcol h5{font-size:15px;font-weight:600;text-transform:uppercase;margin-bottom:18px}
.fcol li{list-style:none;font-size:11.5px;line-height:25px}
.fcol li::before{content:"\25B8";margin-right:6px}
.fcol p{font-size:11.5px;line-height:19px}
.news-form{display:flex;margin-top:12px}
.news-input{width:152px;height:30px;background:var(--white);color:#888;font-size:11px;padding:8px 10px}
.news-btn{width:56px;height:30px;background:#1d1d1d;color:var(--white);font-size:12px;display:flex;align-items:center;justify-content:center}
.socials{display:flex;gap:14px;margin-top:22px;margin-left:8px}
.socials span{width:34px;height:34px;border-radius:50%;border:1.5px solid var(--white)}
.bottom{top:2793px;left:0;width:1200px;height:64px;background:var(--footer-bar);color:#ddd;font-size:11.5px;display:flex;align-items:center;justify-content:center}
</style>
</head>
<body>

<section class="abs hero" role="img" aria-label="Blurred molecular structure photograph in grey and blue tones"></section>
<div class="abs brand"><span class="brand-dot"></span>Plume KEV</div>
<nav class="abs nav"><span class="active">Home</span><span>About us</span><span>Services</span><span>Products</span><span>Blog</span><span>News</span><span>Contacts</span></nav>
<div class="abs login">LOGIN</div>
<h1 class="abs center hero-title">PLUME KEV</h1>
<p class="abs center hero-sub">We develop the machine learning solutions especially focused<br>on deep learning algorithms for biology industry</p>
<div class="abs btn-outline hero-btn">Get start now &nbsp;»</div>
<div class="abs arrow" style="left:59px"><svg width="10" height="14"><path d="M8 1 2 7l6 6" stroke="#fff" stroke-width="2" fill="none"/></svg></div>
<div class="abs arrow" style="left:1108px"><svg width="10" height="14"><path d="M2 1l6 6-6 6" stroke="#fff" stroke-width="2" fill="none"/></svg></div>

<section class="abs services"></section>
<h2 class="abs center section-title" style="top:696px">Our <span>Services</span></h2>
<p class="abs center section-sub" style="top:740px">Neque porro quisquam est qui dolorem ipsum quia dolor sit ame</p>
<div class="abs service" style="left:92px">
  <div class="ring"><svg width="44" height="36" viewBox="0 0 44 36" fill="#0f8a5a"><rect x="14" y="0" width="16" height="14"/><rect x="4" y="18" width="16" height="14"/><rect x="24" y="18" width="16" height="14"/></svg></div>
  <h3>Learning Algorithms</h3>
  <p>Neque porro quisquam est qui dolorem ipsum quia<br>dolor sit amet, consectetur, adipisci velit</p>
</div>
<div class="abs service" style="left:451px">
  <div class="ring"><svg width="40" height="40" viewBox="0 0 40 40" fill="none" stroke="#0f8a5a" stroke-width="6"><circle cx="20" cy="20" r="14"/></svg></div>
  <h3>Biology Industry</h3>
  <p>Neque porro quisquam est qui dolorem ipsum quia<br>dolor sit amet, consectetur, adipisci velit</p>
</div>
<div class="abs service" style="left:811px">
  <div class="ring"><svg width="30" height="34" viewBox="0 0 30 34" fill="#0f8a5a"><circle cx="15" cy="9" r="8"/><path d="M1 34c0-10 6-15 14-15s14 5 14 15z"/></svg></div>
  <h3>Doctors Diagnose</h3>
  <p>Neque porro quisquam est qui dolorem ipsum quia<br>dolor sit amet, consectetur, adipisci velit</p>
</div>

<section class="abs solutions" role="img" aria-label="Green background with faint DNA strand imagery"></section>
<h2 class="abs center section-title" style="top:1118px;color:var(--white);font-size:25px">Machine Learning Solutions Especially</h2>
<p class="abs center section-sub" style="top:1158px;color:#e4f3ea">Lorem Ipsum is simply dummy text of the printing and typesetting industry</p>
<div class="abs monitor"><div class="monitor-screen"><span class="brand-dot" style="width:22px;height:22px"></span>Plume KEV</div></div>
<div class="abs stand"></div>
<div class="abs base"></div>
<div class="abs sol-text">
  <h2>Neque porro quisquam est qui dolorem ipsum quia dolor</h2>
  <p>Lorem Ipsum has been the industry's standard dummy text ever since the 1500s, when an unknown printer took a galley of type and scrambled it to make a type specimen book. It has survived not only five centuries, but also the leap into electronic typesetting, remaining essentially unchanged.</p>
  <p>It was popularised in the 1960s with the release of Transet sheets containing Lorem Ipsum passages, and more recently with desktop publishing software like Folio Layout</p>
</div>
<div class="abs btn-outline sol-btn" style="text-transform:none">Read More</div>

<section class="abs testimonial" role="img" aria-label="Dark laboratory photograph background"></section>
<div class="abs avatar" role="img" aria-label="Portrait photo of the client"></div>
<span class="abs qmark" style="top:1782px;left:146px">“</span>
<p class="abs quote">Lorem Ipsum has been the industry's standard dummy text ever since the 1500s, when an unknown printer took a galley of type and scrambled it to make a type specimen book. It has survived not only five centuries, but also the leap into electronic typesetting, remaining essentially unchanged. It was popularised in the 1960s with the release of Transet sheets containing Lorem Ipsum passages</p>
<span class="abs qmark" style="top:1832px;left:966px">”</span>
<p class="abs center author">Marc Levin<br>Ohio, United States</p>

<section class="abs products"></section>
<h2 class="abs center section-title" style="top:1996px">Our <span>Product</span></h2>
<p class="abs center section-sub" style="top:2038px">Neque porro quisquam est qui dolorem ipsum quia dolor sit ame</p>
<article class="abs card" style="left:86px"><div class="card-img" role="img" aria-label="Gloved hands handling lab samples" style="background:linear-gradient(135deg,#2d5f8a,#9fbdd6)"></div><h4>Neque porro quisquam</h4><p>Lorem ipsum dolor sit amet, consectur<br>scing elit, sed do eiusmod tempor</p></article>
<article class="abs card" style="left:345px"><div class="card-img" role="img" aria-label="Scientists working in a blue-lit laboratory" style="background:linear-gradient(135deg,#1f4f8f,#7fa8d8)"></div><h4>Neque porro quisquam</h4><p>Lorem ipsum dolor sit amet, consectur<br>scing elit, sed do eiusmod tempor</p></article>
<article class="abs card" style="left:604px"><div class="card-img" role="img" aria-label="Researcher examining a plant sample" style="background:linear-gradient(135deg,#e9efe8,#9fb79a)"></div><h4>Neque porro quisquam</h4><p>Lorem ipsum dolor sit amet, consectur<br>scing elit, sed do eiusmod tempor</p></article>
<article class="abs card" style="left:863px"><div class="card-img" role="img" aria-label="Laboratory glassware with orange liquid" style="background:linear-gradient(135deg,#cfe0ee,#d98a4e)"></div><h4>Neque porro quisquam</h4><p>Lorem ipsum dolor sit amet, consectur<br>scing elit, sed do eiusmod tempor</p></article>

<section class="abs partners"></section>
<div class="abs partner" style="left:132px"></div>
<div class="abs partner" style="left:338px"></div>
<div class="abs partner" style="left:544px"></div>
<div class="abs partner" style="left:748px"></div>
<div class="abs partner" style="left:952px"></div>

<footer class="abs footer"></footer>
<div class="abs fcol" style="left:88px"><h5>Links</h5><ul><li>Home</li><li>About Us</li><li>Past Performance</li><li>Pricing</li><li>Contact</li></ul></div>
<div class="abs fcol" style="left:328px;width:236px"><h5>The Symptoms</h5><p>Lorem Ipsum has been the industry's standard dummy text ever since the 1500s, when an unknown printer took</p><p style="margin-top:6px">a galley of type and scrambled it to make a type specimen book. It has survived not only five centuries, but also the leap into</p></div>
<div class="abs fcol" style="left:679px;width:190px"><h5>Get In Touch</h5><p>Address : 1450 Harbor Lane,<br>Riverton, NJ</p><p style="margin-top:14px">Phone : 00 123 456 7890</p><p style="margin-top:14px">Email : info@plumekev.com</p></div>
<div class="abs fcol" style="left:908px;width:210px"><h5>Newsletter</h5><p>Your about us information would fit here nicely.</p><div class="news-form"><div class="news-input">Email address</div><div class="news-btn">Submit</div></div><div class="socials"><span></span><span></span><span></span></div></div>
<div class="abs bottom">Copyright © 2016. All Rights Reserved</div>

</body>
</html>
```